Eyecatching website design for commercial lighting business

This contest is all about the graphic design aspect. We need a striking website design for a commercial lighting company. We want something really eye catching to introduce people to our range of induction and LED lights which save businesses money on maintenance and electricity costs.

To be successful in this contest you will need to provide a design and pictures for the pages listed below.

We are using the platform velbrin.com.au and you can see the attached template which everything will be loaded into so we just need HTML files which we can upload and we can do everything else from Velbrin.

The final design should be strong and clean and use the colours and textures in the attached business card file.

Detailed requirements:

Please see attached screenshot of the website template, all we need is a fantastic graphic design and improvement/ incorporation of our logo for the following pages
Page Headings:
1. Home
About Us, Contact Us, snapshot of and link to Blog

Each of the below pages will have several paragraphs of text followed by a list of suitable products which is generated from our product catalogue.

2. Car Park Lighting
3. Educational Lighting
4. Hospitality Lighting
5. Office & Shop Lighting
6. Warehouse Lighting

Some of the website we have seen which are similar in nature are:
http://www.quorvanlamps.com.au/
http://www.tibrox.com/
http://www.gandowlumen.net/commercial-led
but we really want a modern, eye catching and memorable design

Some of the designs built on Velbrin that we like are:

http://www.pemberhollow.com.au/
http://www.marwickgoods.com.au/
http://www.kelmorabay.com.au/

I've also uploaded a couple of photos that we love. We'd like something similar for each industry.

Target Market(s)

Company Owners, Maintenance & Facilities Managers, Electrical Contractors

Industry/Entity Type

Electrical

Coding

Coded - Design and coding required

Number of Pages Required

5+ page

Font styles to use
Sans Serif

Colors
33a6d7
ec1f27

Requirements
Must have
• -Must scale to mobile
• -HTML coded files need to be provided (HTML Bootstrap)
Nice to have
• -Prefer incorporation of our logo into header bar
• -Design of 2-3 advertising banners which can be displayed on the home page
• -Prominent call to action button towards top of page 'Get a quote' or similar
• -Grid based design HTML Bootstrap

```html
<!DOCTYPE html>
<html lang="en">
<head>
<meta charset="utf-8">
<title>Brightmere Lighting – Commercial Lighting</title>
<link href="https://fonts.googleapis.com/css2?family=Open+Sans:wght@400;600;700;800&display=swap" rel="stylesheet">
<style>
:root{
  --red:#ec1f27;
  --blue:#33a6d7;
  --dark:#1d1d1f;
  --darker:#141415;
  --ink:#333;
  --muted:#777;
  --white:#fff;
}
*{box-sizing:border-box;margin:0;padding:0}
html,body{width:698px;height:1200px;overflow:hidden}
body{font-family:"Open Sans",Arial,sans-serif;color:var(--ink);background:var(--white);font-size:9px;line-height:1.5}
.page{width:698px;height:1200px;position:relative}

/* header */
.site-header{height:48px;background:var(--dark);display:flex;align-items:center;justify-content:space-between;padding:0 22px}
.brand{display:flex;align-items:center;gap:7px}
.brand-mark{width:12px;height:12px;background:var(--red)}
.brand-name{color:var(--white);font-weight:700;font-size:12px;letter-spacing:.3px}
.header-right{text-align:right}
.call{color:var(--white);font-size:8px;font-weight:700;letter-spacing:.4px}
.call span{color:var(--red)}
.main-nav{display:flex;gap:16px;margin-top:6px;justify-content:flex-end}
.main-nav a{color:var(--white);font-size:7.5px;font-weight:700;text-decoration:none;text-transform:uppercase}
.main-nav a.active{color:var(--red)}

/* hero */
.hero{position:relative;height:272px}
.hero-photo{position:absolute;inset:0;background:linear-gradient(100deg,#4b4237 0%,#a59a8a 30%,#e8e4dc 50%,#b9a27b 72%,#6e5a3d 100%)}
.hero-content{position:absolute;top:84px;left:0;right:0;text-align:center}
.hero-title{color:var(--white);font-size:24px;font-weight:800;line-height:1.15;text-transform:uppercase;text-shadow:0 2px 6px rgba(0,0,0,.45)}
.btn{display:inline-block;background:var(--blue);color:var(--white);font-size:7.5px;font-weight:700;padding:7px 12px;text-transform:uppercase;text-decoration:none}
.hero .btn{margin-top:14px}
.dots{position:absolute;bottom:10px;left:0;right:0;display:flex;justify-content:center;gap:5px}
.dots i{width:6px;height:6px;border-radius:50%;background:rgba(255,255,255,.6)}
.dots i.on{background:var(--red)}

/* welcome */
.welcome{display:flex;gap:26px;padding:28px 22px 0;height:250px}
.welcome-text{flex:1}
.welcome-text h2{font-size:11.5px;font-weight:800;line-height:1.3;text-transform:uppercase;color:var(--ink);margin-bottom:8px}
.welcome-text p{color:var(--muted);font-size:7px;margin-bottom:7px}
.welcome-text .lead{font-weight:700;color:var(--ink)}
.ticks{list-style:none;margin-bottom:8px}
.ticks li{display:flex;gap:5px;font-size:7px;color:var(--muted);margin-bottom:3px}
.ticks svg{flex:none;margin-top:1px}
.more{color:var(--blue);font-weight:700;font-size:7px;text-decoration:none}
.video{width:318px;height:176px;background:var(--darker);position:relative}
.video-bar{height:18px;display:flex;justify-content:space-between;align-items:center;padding:0 7px;color:var(--white);font-size:6.5px}
.video-frame{position:absolute;top:18px;left:0;right:0;bottom:0;background:linear-gradient(135deg,#3b3a38,#8c8478 55%,#cfc6b6)}
.play{position:absolute;left:50%;top:50%;transform:translate(-50%,-50%);width:36px;height:24px;background:rgba(0,0,0,.75);border-radius:5px;display:flex;align-items:center;justify-content:center}

/* services */
.services{background:var(--red);height:198px;padding-top:32px;text-align:center;color:var(--white)}
.section-title{font-size:12px;font-weight:800;text-transform:uppercase;letter-spacing:.4px}
.services .section-title::after{content:"";display:block;width:26px;height:2px;background:var(--white);margin:5px auto 0}
.service-list{display:flex;justify-content:center;gap:36px;margin-top:22px}
.service{width:80px;text-align:center}
.service-icon{width:66px;height:66px;border:3px solid var(--white);border-radius:50%;margin:0 auto 10px;display:flex;align-items:center;justify-content:center}
.service-name{font-size:6.5px;font-weight:700;text-transform:uppercase}

/* products + blog */
.showcase{display:flex;gap:26px;padding:22px 22px 0;height:272px}
.showcase h3{font-size:11px;font-weight:800;text-transform:uppercase;margin-bottom:12px}
.products{width:310px}
.product-grid{display:grid;grid-template-columns:repeat(4,70px);gap:12px 10px}
.product{height:76px}
.p1{background:linear-gradient(135deg,#232323,#8a7b5e)}
.p2{background:linear-gradient(135deg,#e8e2d4,#b79a5a)}
.p3{background:linear-gradient(135deg,#2a2a2a,#c9b27a)}
.p4{background:linear-gradient(135deg,#cfd5da,#7f8a91)}
.p5{background:linear-gradient(135deg,#7a2a23,#2c1c18)}
.p6{background:linear-gradient(135deg,#dad5cb,#8f8779)}
.p7{background:linear-gradient(135deg,#3a2f2c,#b04a3a)}
.p8{background:linear-gradient(135deg,#1c2a36,#6f8fa8)}
.blog{flex:1}
.post{display:flex;gap:10px;margin-bottom:12px}
.post-thumb{width:62px;height:44px;flex:none}
.t1{background:linear-gradient(135deg,#efe9da,#9d8a66)}
.t2{background:linear-gradient(135deg,#c9c4ba,#5e584d)}
.t3{background:linear-gradient(135deg,#e5e3dd,#a8a49a)}
.post-title{color:var(--red);font-size:6.8px;font-weight:700;text-transform:uppercase;line-height:1.35}
.post-meta{display:flex;gap:10px;color:var(--blue);font-size:6px;margin-top:4px}

/* footer */
.site-footer{position:absolute;left:0;right:0;top:1040px;bottom:0;background:var(--dark);color:#bbb}
.footer-cols{display:flex;gap:30px;padding:20px 22px 0}
.footer-col h4{color:var(--white);font-size:9px;font-weight:800;text-transform:uppercase;margin-bottom:8px}
.footer-col p{font-size:6.8px;line-height:1.55}
.col-about{width:180px}
.col-news{width:210px}
.col-contact{flex:1}
.field{margin-top:6px;height:15px;width:140px;background:#2c2c2e;border:1px solid #444;font-size:6.3px;color:#888;padding:2px 6px}
.btn-red{display:inline-block;margin-top:6px;background:var(--red);color:var(--white);font-size:6.3px;font-weight:700;padding:3px 8px;text-transform:uppercase}
.contact-line{display:flex;gap:6px;align-items:flex-start;font-size:6.8px;margin-bottom:4px}
.contact-line svg{flex:none;margin-top:1px}
.socials{display:flex;gap:5px;margin-top:6px}
.socials i{width:13px;height:13px;background:#3a3a3c}
.footer-bottom{position:absolute;left:0;right:0;bottom:0;height:22px;background:var(--darker);font-size:6.3px;color:#888;display:flex;align-items:center;padding:0 22px}
</style>
</head>
<body>
<div class="page">

  <header class="site-header">
    <div class="brand">
      <span class="brand-mark"></span>
      <span class="brand-name">Brightmere Lighting</span>
    </div>
    <div class="header-right">
      <div class="call">CALL US NOW : <span>1 300 482 915</span></div>
      <nav class="main-nav">
        <a class="active" href="#">Home</a>
        <a href="#">About Us</a>
        <a href="#">Products</a>
        <a href="#">Blog</a>
        <a href="#">Contact Us</a>
      </nav>
    </div>
  </header>

  <section class="hero">
    <div class="hero-photo" role="img" aria-label="Bright commercial interiors lit by ceiling panels: a classroom and a hotel reception"></div>
    <div class="hero-content">
      <h1 class="hero-title">Brightmere<br>Lighting</h1>
      <a class="btn" href="#">Get More Information</a>
    </div>
    <div class="dots"><i class="on"></i><i></i><i></i></div>
  </section>

  <section class="welcome">
    <div class="welcome-text">
      <h2>Welcome to the commercial lighting division of Brightmere Lighting</h2>
      <p>Retrofitting old lighting in a commercial or industrial premises is a great way to save money on energy and maintenance costs. New induction and LED fittings last longer, run cooler and cut your power bill while improving light quality for staff and customers in every space.</p>
      <p class="lead">We make it an easy process by providing you with:</p>
      <ul class="ticks">
        <li><svg width="7" height="7" viewBox="0 0 10 10"><path d="M1 5l3 3 5-6" fill="none" stroke="#33a6d7" stroke-width="2"/></svg>The best range of energy saving commercial and industrial lighting</li>
        <li><svg width="7" height="7" viewBox="0 0 10 10"><path d="M1 5l3 3 5-6" fill="none" stroke="#33a6d7" stroke-width="2"/></svg>High quality products from reputable manufacturers which meet Australian standards</li>
        <li><svg width="7" height="7" viewBox="0 0 10 10"><path d="M1 5l3 3 5-6" fill="none" stroke="#33a6d7" stroke-width="2"/></svg>Assistance to ensure you choose the right product for the right application</li>
      </ul>
      <a class="more" href="#">READ MORE »</a>
    </div>
    <div class="video">
      <div class="video-bar"><span>Brightmere Lighting</span><span>&lt;</span></div>
      <div class="video-frame" role="img" aria-label="Video still of a lit hotel lobby with columns"></div>
      <div class="play"><svg width="12" height="12" viewBox="0 0 10 10"><path d="M2 1l7 4-7 4z" fill="#fff"/></svg></div>
    </div>
  </section>

  <section class="services">
    <h2 class="section-title">Our Services</h2>
    <div class="service-list">
      <div class="service">
        <div class="service-icon"><svg width="30" height="24" viewBox="0 0 30 24" fill="#fff"><path d="M6 4h18l4 8v9h-4v-3H6v3H2v-9z"/><rect x="8" y="6" width="14" height="5" fill="#ec1f27"/><circle cx="8" cy="14" r="2" fill="#ec1f27"/><circle cx="22" cy="14" r="2" fill="#ec1f27"/></svg></div>
        <div class="service-name">Car Park Lighting</div>
      </div>
      <div class="service">
        <div class="service-icon"><svg width="30" height="24" viewBox="0 0 30 24" fill="#fff"><path d="M15 3l14 6-14 6L1 9z"/><path d="M7 12v6c3 3 13 3 16 0v-6l-8 4z"/><rect x="26" y="9" width="1.5" height="9"/></svg></div>
        <div class="service-name">Educational Lighting</div>
      </div>
      <div class="service">
        <div class="service-icon"><svg width="30" height="24" viewBox="0 0 30 24" fill="#fff"><path d="M5 6h16v8a6 6 0 0 1-6 6h-4a6 6 0 0 1-6-6z"/><path d="M21 8h3a3 3 0 0 1 0 6h-3v-2h3a1 1 0 0 0 0-2h-3z"/><rect x="3" y="21" width="20" height="2"/></svg></div>
        <div class="service-name">Hospitality Lighting</div>
      </div>
      <div class="service">
        <div class="service-icon"><svg width="30" height="24" viewBox="0 0 30 24" fill="#fff"><path d="M11 3h8v3h-2V5h-4v1h-2z"/><rect x="3" y="6" width="24" height="15" rx="2"/><rect x="3" y="12" width="24" height="1.5" fill="#ec1f27"/><rect x="13" y="11" width="4" height="4" fill="#ec1f27"/></svg></div>
        <div class="service-name">Office Lighting</div>
      </div>
      <div class="service">
        <div class="service-icon"><svg width="30" height="24" viewBox="0 0 30 24" fill="#fff"><path d="M2 9L15 2l13 7v13H2z"/><rect x="7" y="11" width="16" height="11" fill="#ec1f27"/><rect x="8" y="12" width="14" height="2"/><rect x="8" y="15" width="14" height="2"/><rect x="8" y="18" width="14" height="2"/></svg></div>
        <div class="service-name">Warehouse Lighting</div>
      </div>
    </div>
  </section>

  <section class="showcase">
    <div class="products">
      <h3>Our Products</h3>
      <div class="product-grid">
        <div class="product p1" role="img" aria-label="LED panel light"></div>
        <div class="product p2" role="img" aria-label="High bay induction lamp"></div>
        <div class="product p3" role="img" aria-label="Round industrial light fitting"></div>
        <div class="product p4" role="img" aria-label="Flood light"></div>
        <div class="product p5" role="img" aria-label="Lit restaurant interior"></div>
        <div class="product p6" role="img" aria-label="Office with ceiling lighting"></div>
        <div class="product p7" role="img" aria-label="Warm lit hallway"></div>
        <div class="product p8" role="img" aria-label="Car park at night"></div>
      </div>
    </div>
    <div class="blog">
      <h3>Blog</h3>
      <article class="post">
        <div class="post-thumb t1" role="img" aria-label="Lit reception area"></div>
        <div><div class="post-title">Simple steps to cut your lighting costs in commercial buildings</div>
        <div class="post-meta"><span>12/03/2015</span><span>12:45 PM</span><span>Lighting</span></div></div>
      </article>
      <article class="post">
        <div class="post-thumb t2" role="img" aria-label="Warehouse ceiling lights"></div>
        <div><div class="post-title">Why induction lights suit high ceiling warehouses and depots</div>
        <div class="post-meta"><span>08/03/2015</span><span>10:20 AM</span><span>Lighting</span></div></div>
      </article>
      <article class="post">
        <div class="post-thumb t3" role="img" aria-label="Classroom with panel lights"></div>
        <div><div class="post-title">Better learning spaces with bright LED panel lights in schools</div>
        <div class="post-meta"><span>02/03/2015</span><span>09:10 AM</span><span>Lighting</span></div></div>
      </article>
    </div>
  </section>

  <footer class="site-footer">
    <div class="footer-cols">
      <div class="footer-col col-about">
        <h4>About Us</h4>
        <p>Retrofitting old lighting in a commercial or industrial premises is a great way to save money on energy and maintenance costs. Our team makes it simple to find the right fitting for your site.</p>
      </div>
      <div class="footer-col col-news">
        <h4>Newsletter Subscription</h4>
        <p>Register your email to get the latest product news and offers.</p>
        <div class="field">Email Address</div>
        <span class="btn-red">Subscribe</span>
      </div>
      <div class="footer-col col-contact">
        <h4>Contact Us</h4>
        <div class="contact-line"><svg width="7" height="9" viewBox="0 0 10 13"><path d="M5 0a5 5 0 0 1 5 5c0 4-5 8-5 8S0 9 0 5a5 5 0 0 1 5-5z" fill="#ec1f27"/></svg><span>Unit 4, 27 Carrow Street, Brisbane QLD 4000</span></div>
        <div class="contact-line"><svg width="8" height="8" viewBox="0 0 10 10"><path d="M2 0l2 3-1 1c1 2 2 3 3 3l1-1 3 2-1 2C4 10 0 6 0 1z" fill="#ec1f27"/></svg><span>1 300 482 915</span></div>
        <div class="contact-line"><svg width="8" height="7" viewBox="0 0 10 8"><rect width="10" height="8" fill="#ec1f27"/><path d="M0 0l5 4 5-4" fill="none" stroke="#1d1d1f"/></svg><span>hello@brightmere.com.au</span></div>
        <div class="socials"><i></i><i></i><i></i><i></i></div>
      </div>
    </div>
    <div class="footer-bottom">© 2015 Brightmere Lighting. All rights reserved.</div>
  </footer>

</div>
</body>
</html>
```